Präsentationsvorlagen für Unternehmensberatung im Finanzbereich
Zielgruppe
Unternehmensberatung für den Finanzbereich, Compliance Beratung/Implementierung regulatorischer Projekte, Bereitstellung von Management Resourcen, Trainings/Coaching/Seminare. Zielgruppe: Banken, Fonds und Investmentgesellschaften
Aufgabenstellung
hochwertiges design, clean, keine standard bilder von Bergen, Tastaturen oder Menschen, die sich unterhalten. eher Architektur Bilder, Bilder sollen Bezug zum Inhalt haben, Verlässlichkeit, Professionalität, Kundenfokus ausstrahlen. 4 Services sollen präsentiert werden, ggf mit Bildlogo in unterschiedlichen Farben verbinden.

```html
<!DOCTYPE html>
<html lang="en">
<head>
<meta charset="utf-8">
<title>Varendorf Sàrl – Company Presentation Templates</title>
<link href="https://fonts.googleapis.com/css2?family=Open+Sans:wght@300;400;600;700&display=swap" rel="stylesheet">
<style>
:root{
  --page:#ffffff;
  --frame:#efefef;
  --ink:#4b5162;
  --ink-soft:#6b7180;
  --band:#8eaebb;
  --tile:#5a6171;
  --mist:#dde7ec;
  --accent:#7fa6b6;
  --label:#222;
}
*{margin:0;padding:0;box-sizing:border-box}
html,body{width:1200px;height:2400px;overflow:hidden;background:var(--page);font-family:"Open Sans",Arial,sans-serif;color:var(--ink)}
.canvas{position:relative;width:1200px;height:2400px}
.row-label{position:absolute;left:68px;font-size:8px;color:var(--label)}
.board{position:absolute;width:411px;height:238px;background:var(--frame)}
.board.left{left:241px}
.board.right{left:697px}
.slide{position:absolute;left:21px;top:17px;width:365px;height:202px;overflow:hidden;background:#f6f6f6;box-shadow:0 1px 3px rgba(0,0,0,.12)}
.photo{position:absolute}
.band{position:absolute;left:0;right:0;bottom:0;height:19px;background:var(--band);display:flex;align-items:center;justify-content:center;color:#fff;font-size:4px;font-weight:700;letter-spacing:1.2px}
.band .page{position:absolute;right:10px;top:6px;width:7px;height:7px;border:.6px solid #fff;font-size:3.5px;display:flex;align-items:center;justify-content:center;letter-spacing:0}
.band .place{position:absolute;right:14px;font-size:3.5px;font-weight:400}
.vertical{position:absolute;right:6px;bottom:26px;transform-origin:right bottom;transform:rotate(-90deg) translateX(100%);font-size:3.3px;letter-spacing:.8px;color:var(--ink-soft);white-space:nowrap}
.brand{position:absolute;left:0;right:0;text-align:center}
.brand .square{display:inline-block;width:22px;height:22px;border:2.5px solid var(--ink)}
.brand .name{font-size:17px;letter-spacing:4px;font-weight:400;margin-top:10px}
.brand .suffix{font-size:7px;letter-spacing:3px;margin-top:2px;display:flex;align-items:center;justify-content:center;gap:8px}
.brand .suffix::before,.brand .suffix::after{content:"";width:38px;height:.7px;background:currentColor}
.mini-brand{position:absolute;top:12px;left:0;right:0;text-align:center;font-size:5px;font-weight:700;letter-spacing:1.5px;color:var(--ink)}
.section-title{position:absolute;left:22px;top:32px;font-size:17px;font-weight:400;letter-spacing:4px;line-height:25px;color:var(--ink)}
.fine{font-size:3.4px;line-height:4.6px;color:#333}
.fine b{font-weight:700}
.col{position:absolute}
.fact-num{font-size:8px;letter-spacing:.8px;color:var(--accent);font-weight:600}
.fact-sub{font-size:4px;font-weight:600;letter-spacing:.3px;margin:1px 0 4px;color:var(--ink)}
.rule{height:.6px;background:#9fb6c0;margin:8px 0 12px;width:110px}
.list-title{font-size:4px;font-weight:600;letter-spacing:.3px;margin-bottom:5px}
.list-item{font-size:3.3px;line-height:7.5px;color:#333}
.tile{position:absolute;width:141px;height:52px;background:var(--tile);border-radius:3px;display:flex;align-items:center;color:#fff;font-size:6.5px;letter-spacing:1.8px;line-height:9px;font-weight:300}
.tile svg{width:18px;height:18px;margin:0 12px 0 13px;flex:none}
.service-title{position:absolute;left:0;right:0;top:42px;text-align:center;font-size:11px;font-weight:700;letter-spacing:3.2px;line-height:16px;color:var(--ink)}
.service-rule{position:absolute;left:95px;right:95px;top:98px;height:.5px;background:rgba(75,81,98,.2)}
.service-icon{position:absolute;left:64px;top:112px;width:28px;height:28px}
.service-text{position:absolute;left:128px;top:102px;width:172px}
.pill-row{position:absolute;left:214px;top:140px;display:flex;gap:5px}
.pill{width:52px;height:7px;background:#f4f6f8;border:.4px solid #c9d2d8;font-size:3px;display:flex;align-items:center;justify-content:center;letter-spacing:.4px}
.quote{position:absolute;left:155px;top:139px;width:112px;text-align:center;font-size:3px;font-weight:700;line-height:4.4px;letter-spacing:.3px}
.quote::before,.quote::after{position:absolute;top:1px;font-size:9px;font-weight:400}
.quote::before{content:"»";left:-12px}
.quote::after{content:"«";right:-12px}
.contact-band{position:absolute;left:0;right:0;bottom:0;height:19px;background:var(--band);display:flex;justify-content:space-around;align-items:center;padding:0 40px;color:#fff;font-size:3px;font-weight:700;letter-spacing:.4px;white-space:nowrap}
</style>
</head>
<body>
<div class="canvas">

  <p class="row-label" style="top:210px">Titel / Start</p>
  <section class="board left" style="top:95px">
    <div class="slide">
      <div class="photo" style="right:0;top:0;width:80px;height:100px;background:radial-gradient(ellipse at 70% 45%,#3f5a40 0%,#6f8d6c 45%,rgba(246,246,246,0) 72%)" role="img" aria-label="Dark green tropical leaves in the top right corner"></div>
      <div class="photo" style="left:0;bottom:19px;width:85px;height:42px;background:radial-gradient(ellipse at 35% 80%,#3e5a3f 0%,#6c8a69 45%,rgba(246,246,246,0) 72%)" role="img" aria-label="Tropical leaf reaching in from the bottom left corner"></div>
      <div class="brand" style="top:56px">
        <span class="square"></span>
        <div class="name">VARENDORF</div>
        <div class="suffix">SÀRL</div>
      </div>
      <div class="band">COMPANY PRESENTATION<span class="place">FRANKFURT | 2022</span></div>
    </div>
  </section>

  <p class="row-label" style="top:558px">Folie / Zusammenfassung</p>
  <section class="board left" style="top:430px">
    <div class="slide" style="background:linear-gradient(90deg,#f3f3f4 0%,#ececee 55%,#d7d8db 100%)">
      <div class="photo" style="right:0;top:0;width:150px;height:202px;background:linear-gradient(200deg,#2e3136 0%,#8e9196 40%,rgba(236,236,238,0) 75%),linear-gradient(0deg,#3b3e44 0%,rgba(236,236,238,0) 30%)" role="img" aria-label="Glass skyscraper facade photographed from below"></div>
      <h2 class="section-title">EXECUTIVE<br>SUMMARY</h2>
    </div>
  </section>
  <section class="board right" style="top:430px">
    <div class="slide" style="background:#f7f7f8">
      <div class="photo" style="right:0;top:0;width:140px;height:202px;background:linear-gradient(200deg,#c9cbcf 0%,rgba(247,247,248,0) 65%)" role="img" aria-label="Faint glass skyscraper facade in the background"></div>
      <div class="mini-brand">VARENDORF</div>
      <div class="col fine" style="left:48px;top:68px;width:140px">
        <p>Our advisory work supports banks, funds and investment firms with clear structures, reliable governance and practical compliance solutions across Europe.</p><br>
        <p>We combine regulatory expertise with hands-on experience to deliver projects on time and on budget.</p>
      </div>
      <div class="col fine" style="left:196px;top:68px;width:135px">
        <p>Founded in Frankfurt, the firm brings senior management experience to every mandate and stays close to each client.</p><br>
        <p>Our approach is personal, discreet and focused on long-term partnership.</p><br>
        <p><b>Trusted advice for the financial sector.</b></p>
      </div>
      <div class="vertical">COMPANY PRESENTATION</div>
      <div class="band">EXECUTIVE SUMMARY<span class="page">2</span></div>
    </div>
  </section>

  <p class="row-label" style="top:837px">Folie / Unternehmensvorstellung</p>
  <section class="board left" style="top:727px">
    <div class="slide" style="background:#ededed">
      <div class="photo" style="left:137px;top:0;width:228px;height:202px;background:linear-gradient(150deg,#f1f1f1 0%,#dcdcdc 45%,#8d8d8d 100%)" role="img" aria-label="Concrete staircase with a steel handrail"></div>
      <h2 class="section-title">ABOUT</h2>
    </div>
  </section>
  <section class="board right" style="top:727px">
    <div class="slide" style="background:#f7f7f8">
      <div class="photo" style="right:0;top:0;width:120px;height:202px;background:linear-gradient(150deg,rgba(247,247,248,0) 30%,#dedfe1 100%)" role="img" aria-label="Faint staircase in the background"></div>
      <div class="mini-brand">VARENDORF</div>
      <div class="col" style="left:44px;top:50px;width:120px">
        <div class="fact-num">18+YEARS</div>
        <div class="fact-sub">OF EXPERIENCE IN THE FINANCIAL SECTOR</div>
        <p class="fine">Senior roles in banking and fund management with a focus on governance, risk and regulatory change.</p>
        <div class="rule"></div>
        <div class="list-title">QUALIFIED LAWYER</div>
        <p class="list-item">» Admitted to practice law<br>» Focus on financial regulation<br>» Member of professional bodies</p>
      </div>
      <div class="col" style="left:207px;top:50px;width:120px">
        <div class="fact-num">10+YEARS</div>
        <div class="fact-sub">IN EXECUTIVE AND BOARD POSITIONS</div>
        <p class="fine">Board and executive mandates for investment companies and management firms across several jurisdictions.</p>
        <div class="rule"></div>
        <div class="list-title">4 JURISDICTIONS</div>
        <p class="list-item">1) Luxembourg<br>2) Germany<br>3) Switzerland<br>4) Ireland</p>
      </div>
      <div class="vertical">COMPANY PRESENTATION</div>
      <div class="band">ABOUT | QUALIFICATIONS<span class="page">3</span></div>
    </div>
  </section>

  <p class="row-label" style="top:1123px">Folie / Dienstleistungen</p>
  <section class="board left" style="top:1023px">
    <div class="slide" style="background:#ececee">
      <div class="photo" style="left:0;top:0;width:365px;height:202px;background:linear-gradient(90deg,rgba(236,236,238,0) 40%,#b8b7c6 48%,#8c8ea3 56%,#d9d9de 64%,#c7c7c9 100%),linear-gradient(160deg,rgba(0,0,0,0) 55%,#7d7d80 100%)" role="img" aria-label="Mirrored pillar casting shadows on a bright floor"></div>
      <h2 class="section-title">SERVICES</h2>
    </div>
  </section>
  <section class="board right" style="top:1023px">
    <div class="slide" style="background:#f1f1f2">
      <div class="photo" style="left:0;top:0;width:365px;height:202px;background:linear-gradient(90deg,rgba(241,241,242,0) 40%,#d6d6dc 50%,rgba(241,241,242,0) 65%),linear-gradient(160deg,rgba(0,0,0,0) 60%,#b9b9bc 100%)" role="img" aria-label="Faint mirrored pillar in the background"></div>
      <div class="mini-brand">VARENDORF</div>
      <div class="tile" style="left:36px;top:56px"><svg viewBox="0 0 20 20" fill="none" stroke="#fff" stroke-width="1"><circle cx="9" cy="9" r="5"/><circle cx="9" cy="9" r="2"/><path d="M9 2v2M9 14v2M2 9h2M14 9h2M13 17l2-4 3 1"/></svg>INDEPENDENT<br>DIRECTORSHIPS/<br>RC MANDATES</div>
      <div class="tile" style="left:186px;top:56px"><svg viewBox="0 0 20 20" fill="none" stroke="#fff" stroke-width="1"><rect x="3" y="2" width="11" height="15"/><path d="M6 6h5M6 9h5M6 12h3"/><circle cx="15" cy="14" r="3"/></svg>REGULATORY/<br>COMPLIANCE<br>SERVICES</div>
      <div class="tile" style="left:36px;top:118px"><svg viewBox="0 0 20 20" fill="none" stroke="#fff" stroke-width="1"><circle cx="8" cy="8" r="5"/><path d="M12 12l5 5"/><ellipse cx="6" cy="16" rx="4" ry="1.5"/></svg>AML/CTF<br>SUPPORT</div>
      <div class="tile" style="left:186px;top:118px"><svg viewBox="0 0 20 20" fill="none" stroke="#fff" stroke-width="1"><path d="M10 3a5 5 0 0 0-3 9v2h6v-2a5 5 0 0 0-3-9z"/><path d="M8 16h4M8.5 18h3M2 8h2M16 8h2M4 3l1.5 1.5M16 3l-1.5 1.5"/></svg>COACHING/<br>TRAININGS</div>
      <div class="vertical">COMPANY PRESENTATION</div>
      <div class="band">SERVICES<span class="page">4</span></div>
    </div>
  </section>

  <p class="row-label" style="top:1660px">Folien / Dienstleistung einzeln</p>
  <section class="board left" style="top:1408px">
    <div class="slide" style="background:var(--mist)">
      <div class="photo" style="left:0;top:0;width:200px;height:80px;background:linear-gradient(170deg,rgba(221,231,236,0) 20%,#c8d2d6 45%,rgba(221,231,236,0) 70%)" role="img" aria-label="Faint architectural detail of a building edge"></div>
      <div class="mini-brand">VARENDORF</div>
      <h3 class="service-title">INDEPENDENT DIRECTORSHIPS/<br>RC MANDATES</h3>
      <div class="service-rule"></div>
      <svg class="service-icon" viewBox="0 0 20 20" fill="none" stroke="#4b5162" stroke-width=".8"><circle cx="9" cy="9" r="5"/><circle cx="9" cy="9" r="2"/><path d="M9 2v2M9 14v2M2 9h2M14 9h2M13 17l2-4 3 1"/></svg>
      <p class="service-text fine">We act as independent director and conducting officer for funds and management companies, providing sound oversight, clear reporting and reliable governance for every board we serve.</p>
      <div class="vertical">COMPANY PRESENTATION</div>
      <div class="band">SERVICES<span class="page">5</span></div>
    </div>
  </section>
  <section class="board right" style="top:1408px">
    <div class="slide" style="background:var(--mist)">
      <div class="photo" style="left:0;top:0;width:130px;height:183px;background:linear-gradient(100deg,#c3d2d9 0%,#d3dfe5 55%,rgba(221,231,236,0) 100%)" role="img" aria-label="Faint glass tower facade"></div>
      <div class="mini-brand">VARENDORF</div>
      <h3 class="service-title">REGULATORY/<br>COMPLIANCE SERVICES</h3>
      <div class="service-rule"></div>
      <svg class="service-icon" viewBox="0 0 20 20" fill="none" stroke="#4b5162" stroke-width=".8"><rect x="3" y="2" width="11" height="15"/><path d="M6 6h5M6 9h5M6 12h3"/><circle cx="15" cy="14" r="3"/></svg>
      <p class="service-text fine">We support the design and implementation of regulatory projects, from gap analysis and policies to reporting, so that your organisation meets every supervisory requirement with confidence.</p>
      <div class="vertical">COMPANY PRESENTATION</div>
      <div class="band">SERVICES<span class="page">6</span></div>
    </div>
  </section>
  <section class="board left" style="top:1683px">
    <div class="slide" style="background:var(--mist)">
      <div class="photo" style="left:0;top:0;width:365px;height:183px;background:linear-gradient(180deg,#b9bec0 0%,#d3d7d8 30%,#dde5ea 55%,#c9d8e3 100%)" role="img" aria-label="Ornate building cornice against a cloudy sky"></div>
      <div class="mini-brand">VARENDORF</div>
      <h3 class="service-title" style="top:46px">AML/CTF SUPPORT</h3>
      <div class="service-rule"></div>
      <svg class="service-icon" viewBox="0 0 20 20" fill="none" stroke="#4b5162" stroke-width=".8"><circle cx="8" cy="8" r="5"/><path d="M12 12l5 5"/><ellipse cx="6" cy="16" rx="4" ry="1.5"/></svg>
      <p class="service-text fine">We help you build effective anti money laundering and counter terrorist financing frameworks, including risk assessments, controls, reviews and ongoing support for your teams.</p>
      <div class="pill-row"><span class="pill">AML SUPPORT</span><span class="pill">CTF SUPPORT</span></div>
      <div class="vertical">COMPANY PRESENTATION</div>
      <div class="band">SERVICES<span class="page">7</span></div>
    </div>
  </section>
  <section class="board right" style="top:1683px">
    <div class="slide" style="background:var(--mist)">
      <div class="photo" style="left:0;top:0;width:365px;height:183px;background:radial-gradient(circle at 40% 12%,#cfc9b8 0,rgba(221,231,236,0) 18px),radial-gradient(circle at 90% 60%,#d4cebf 0,rgba(221,231,236,0) 22px),radial-gradient(circle at 2% 75%,#d0c9b7 0,rgba(221,231,236,0) 16px)" role="img" aria-label="Climbing wall with holds on a light surface"></div>
      <div class="mini-brand">VARENDORF</div>
      <h3 class="service-title" style="top:46px">COACHING/TRAININGS</h3>
      <div class="service-rule"></div>
      <svg class="service-icon" viewBox="0 0 20 20" fill="none" stroke="#4b5162" stroke-width=".8"><path d="M10 3a5 5 0 0 0-3 9v2h6v-2a5 5 0 0 0-3-9z"/><path d="M8 16h4M8.5 18h3M2 8h2M16 8h2M4 3l1.5 1.5M16 3l-1.5 1.5"/></svg>
      <p class="service-text fine">Tailored seminars and coaching sessions for boards, managers and staff, covering regulation, governance and compliance in a practical and engaging format.</p>
      <p class="quote">PRACTICAL KNOWLEDGE FOR DAILY WORK<br>IN A REGULATED ENVIRONMENT</p>
      <div class="vertical">COMPANY PRESENTATION</div>
      <div class="band">SERVICES<span class="page">8</span></div>
    </div>
  </section>

  <p class="row-label" style="top:2123px">Folie / Kontakt</p>
  <section class="board left" style="top:2015px">
    <div class="slide" style="background:#5d6474">
      <div class="photo" style="left:0;top:0;width:365px;height:183px;background:linear-gradient(90deg,#565d6c 0%,#646b7b 45%,#5b6271 100%)" role="img" aria-label="Dark office interior behind a tinted overlay"></div>
      <div class="brand" style="top:56px;color:#fff">
        <span class="square" style="border-color:#fff"></span>
        <div class="name">VARENDORF</div>
        <div class="suffix">SÀRL</div>
      </div>
      <div class="contact-band">
        <span>VORNAME NAME</span><span>TELEFON 040 715 392</span><span>E-MAIL INFO@VARENDORF.DE</span><span>LINDENALLEE 7</span><span>20354 HAMBURG</span>
      </div>
    </div>
  </section>

</div>
</body>
</html>
```